DESKHAVEN COSPACE Website design and coding

DESKHAVEN COSPACE

DESKHAVEN is Galveston’s first (and currently only) shared business co-working space. We share the same upscale, casual work environment, but we work independently on our own (or our team’s) projects and goals. For only a flat $195 membership fee per month, you have your very own all-inclusive, fun, personal business office environment. Website is written (Word file #12, below); and all pictures etc provided. Galveston is a beachy, coastal, historic city an hour from Houston, Texas USA. Logo (file 11 below) is temporary only.

Target Market(s)

Outside sales people, medical students looking for study hall, Houston companies looking for local office, real estate agents, graphic artists, entrepreneurs, etc

Contact Information for Business Card

will discuss --want to combine with current business card with multiple businesses

Logo Text

DESKHAVEN COSPACE

Coding

Coded - Design and coding required

Number of Pages Required

5+ page

Colors
ec1f27
fbed22

Requirements
Nice to have
• maroon/wine dominant with yellow and red accents, gray base are the colors of the space--website could coordinate--but open to creative ideas/combinations

```html
<!DOCTYPE html>
<html lang="en">
<head>
<meta charset="utf-8">
<title>Deskhaven Cospace – Membership</title>
<link rel="stylesheet" href="https://fonts.googleapis.com/css2?family=Catamaran:wght@400;500;600;700;800&display=swap">
<style>
  :root{
    --maroon:#820000;
    --maroon-deep:#740000;
    --yellow:#ffd600;
    --ink:#222;
    --gray-band:#f2f2f2;
    --white:#fff;
  }
  *{box-sizing:border-box;margin:0;padding:0}
  html,body{width:1200px;height:1200px;overflow:hidden;background:var(--white)}
  body{font-family:"Catamaran",sans-serif;color:var(--ink);position:relative}
  .page{position:absolute;left:306px;top:0;width:588px;height:1200px;background:var(--white)}
  .abs{position:absolute}

  /* header */
  .site-header{left:0;top:0;width:588px;height:30px;background:var(--maroon)}
  .brand{left:55px;top:8px;font-weight:800;font-size:10px;color:var(--yellow);letter-spacing:.2px}
  .nav a{position:absolute;top:10px;font-size:6.6px;color:var(--white);text-decoration:none;font-weight:500}
  .nav a.active{color:var(--yellow)}
  .nav a.active::after{content:"";position:absolute;left:0;right:0;top:10px;height:1.5px;background:var(--yellow)}

  /* hero */
  .hero{left:0;top:30px;width:588px;height:159px;background:linear-gradient(90deg,#3b2a1c,#5a4330 35%,#4a3a2c 60%,#2f251d)}
  .hero::after{content:"";position:absolute;inset:0;background:rgba(30,15,5,.35)}
  .hero-title{left:0;top:56px;width:588px;text-align:center;font-size:20px;font-weight:700;color:var(--white);z-index:1}
  .breadcrumb{left:0;top:95px;width:588px;text-align:center;font-size:6.5px;color:var(--white);z-index:1}
  .breadcrumb span{color:var(--yellow)}

  /* intro */
  .section-title{left:0;top:242px;width:588px;text-align:center;font-size:21px;color:var(--maroon);font-weight:500}
  .section-title b{font-weight:800}
  .rule{height:1.5px;background:var(--yellow)}
  .intro{left:166px;top:292px;width:256px;text-align:center;font-size:6.6px;line-height:10.3px}

  /* pricing */
  .price-card{left:91px;top:376px;width:134px;height:245px;background:var(--maroon);box-shadow:0 1px 3px rgba(0,0,0,.25);color:var(--white)}
  .plan-name{left:0;top:26px;width:134px;text-align:center;font-size:6px;font-weight:700;letter-spacing:.3px}
  .price{left:0;top:46px;width:134px;text-align:center;font-size:16px;font-weight:700}
  .features{left:24px;top:78px;list-style:none}
  .features li{position:relative;height:14.7px;padding-left:9px;font-size:6.4px;line-height:8px}
  .features svg{position:absolute;left:0;top:1px}
  .plan-note{left:0;top:167px;width:134px;text-align:center;font-size:6.4px;line-height:9.3px}
  .btn{display:block;background:var(--yellow);color:#111;border-radius:11px;text-align:center;font-weight:700;font-size:6.4px}
  .join{left:31px;top:200px;width:66px;height:20px;line-height:20px}

  .photo-frame{left:296px;top:401px;width:191px;height:217px;border:4px solid var(--yellow)}
  .portrait{left:313px;top:378px;width:191px;height:218px;background:linear-gradient(135deg,#c9c3b6,#d8c2ab 45%,#a88266 80%,#8e8a86)}

  /* free day */
  .trial{left:0;top:671px;width:588px;height:346px;background:var(--gray-band)}
  .space-main{left:55px;top:31px;width:314px;height:165px;background:linear-gradient(180deg,#9c9488,#5a5048 55%,#3a3532)}
  .space-kitchen{left:55px;top:210px;width:151px;height:94px;background:linear-gradient(135deg,#8c7a5c,#c59b54 50%,#4a3f33)}
  .space-desks{left:218px;top:210px;width:151px;height:94px;background:linear-gradient(135deg,#4a4a4a,#8d8a80 50%,#2c2a22)}
  .trial-title{left:390px;top:30px;font-size:20px;line-height:25.5px;color:var(--maroon);font-weight:500}
  .trial-title b{font-weight:800}
  .trial-text{left:390px;top:104px;width:142px;font-size:6.5px;line-height:10.3px}
  .contact-btn{left:390px;top:158px;width:86px;height:20px;line-height:20px}

  /* footer */
  .site-footer{left:0;top:1017px;width:588px;height:183px;background:var(--maroon);color:var(--white)}
  .state-shape{left:26px;top:50px;width:109px;height:79px;background:radial-gradient(ellipse at center,#7a0000 40%,rgba(130,0,0,0) 75%)}
  .foot-brand{left:55px;top:27px;color:var(--yellow);line-height:11px}
  .foot-brand strong{display:block;font-size:11.5px;font-weight:800}
  .foot-brand span{display:block;font-size:9px;font-weight:400}
  .tagline{left:55px;top:64px;font-size:6.5px;line-height:11.7px}
  .legal{left:55px;top:111px;width:70px;text-align:center;font-size:3.6px;line-height:8.5px}
  .legal a{color:var(--yellow);text-decoration:none}
  .foot-col h4{font-size:8px;font-weight:700;color:var(--yellow)}
  .foot-col .rule{width:43px;margin-top:4px}
  .foot-col ul{list-style:none;margin-top:12px;margin-left:-2px}
  .foot-col li{font-size:6.5px;line-height:11.7px}
  .foot-col li.hl{color:var(--yellow)}
</style>
</head>
<body>
<div class="page">
  <header class="site-header abs">
    <div class="brand abs">DESKHAVEN</div>
    <nav class="nav">
      <a style="left:334px">Home</a>
      <a style="left:369px">About</a>
      <a style="left:405px">Amenities</a>
      <a class="active" style="left:455px">Membership</a>
      <a style="left:509px">Contact</a>
    </nav>
  </header>

  <section class="hero abs" role="img" aria-label="Team members shaking hands around a meeting table"></section>
  <h1 class="hero-title abs">Membership</h1>
  <div class="breadcrumb abs"><span>Home</span> → Membership</div>

  <h2 class="section-title abs"><b>Deskhaven</b> Membership</h2>
  <div class="rule abs" style="left:267px;top:277px;width:42px"></div>
  <p class="intro abs">For only $195 a month, charged to your credit card, you get the all-inclusive amenities for one flat fee.  The only “extras” are for copies, on a per-copy basis. We will bill you automatically monthly on the first of the month unless you cancel.  You need only give us thirty day notice to cancel (but no partial month refunds can be given).</p>

  <div class="price-card abs">
    <div class="plan-name abs">ALL-INCLUSIVE</div>
    <div class="rule abs" style="left:44px;top:39px;width:44px"></div>
    <div class="price abs">$195/month</div>
    <ul class="features abs">
      <li><svg width="6" height="6" viewBox="0 0 6 6"><circle cx="3" cy="3" r="3" fill="#ffd600"/><path d="M1.6 3.1l1 1 1.8-1.9" stroke="#820000" stroke-width=".8" fill="none"/></svg>Wi-fi</li>
      <li><svg width="6" height="6" viewBox="0 0 6 6"><circle cx="3" cy="3" r="3" fill="#ffd600"/><path d="M1.6 3.1l1 1 1.8-1.9" stroke="#820000" stroke-width=".8" fill="none"/></svg>Coffee</li>
      <li><svg width="6" height="6" viewBox="0 0 6 6"><circle cx="3" cy="3" r="3" fill="#ffd600"/><path d="M1.6 3.1l1 1 1.8-1.9" stroke="#820000" stroke-width=".8" fill="none"/></svg>Use of conference room</li>
      <li><svg width="6" height="6" viewBox="0 0 6 6"><circle cx="3" cy="3" r="3" fill="#ffd600"/><path d="M1.6 3.1l1 1 1.8-1.9" stroke="#820000" stroke-width=".8" fill="none"/></svg>Office use</li>
      <li><svg width="6" height="6" viewBox="0 0 6 6"><circle cx="3" cy="3" r="3" fill="#ffd600"/><path d="M1.6 3.1l1 1 1.8-1.9" stroke="#820000" stroke-width=".8" fill="none"/></svg>Use of the kitchen</li>
      <li><svg width="6" height="6" viewBox="0 0 6 6"><circle cx="3" cy="3" r="3" fill="#ffd600"/><path d="M1.6 3.1l1 1 1.8-1.9" stroke="#820000" stroke-width=".8" fill="none"/></svg>Lockers</li>
    </ul>
    <p class="plan-note abs">All other amenities  included<br>(no additional cost)</p>
    <a class="btn join abs">Join Now</a>
  </div>

  <div class="photo-frame abs"></div>
  <div class="portrait abs" role="img" aria-label="Smiling member working at a laptop"></div>

  <section class="trial abs">
    <div class="space-main abs" role="img" aria-label="Open co-working floor with lounge seating and desks"></div>
    <div class="space-kitchen abs" role="img" aria-label="Shared kitchen with long wooden table"></div>
    <div class="space-desks abs" role="img" aria-label="Private desks with yellow gaming chairs"></div>
    <h2 class="trial-title abs"><b>Get A Free Day</b><br>To Try Us Out!</h2>
    <div class="rule abs" style="left:390px;top:88px;width:43px"></div>
    <p class="trial-text abs">Contact us. We’ll call you back with a “smart lock” code and you’re in!<br>After you try us out, and we talk, you can make your first monthly payment.</p>
    <a class="btn contact-btn abs">Contact Us</a>
  </section>

  <footer class="site-footer abs">
    <div class="state-shape abs" role="img" aria-label="Faint state map decoration"></div>
    <div class="foot-brand abs"><strong>DESKHAVEN</strong><span>COSPACE</span></div>
    <p class="tagline abs">Bayport’s first  shared business<br>co-working space</p>
    <p class="legal abs">©2020 Deskhaven. All Rights Reserved.<br><a>Terms of Use | Privacy Policy</a></p>

    <div class="foot-col abs" style="left:235px;top:30px">
      <h4>Menu</h4><div class="rule"></div>
      <ul><li class="hl">Home</li><li>About</li><li>Amenities</li><li>Membership</li><li>Contact</li></ul>
    </div>
    <div class="foot-col abs" style="left:348px;top:30px">
      <h4>Social</h4><div class="rule"></div>
      <ul><li>Folkfeed</li><li>Proline</li><li>Pixboard</li></ul>
    </div>
    <div class="foot-col abs" style="left:460px;top:30px">
      <h4>Contact</h4><div class="rule"></div>
      <ul><li>418 Harbor Ave.</li><li>Ste. 240</li><li>Bayport, TX 77901</li><li>713-555-0148</li><li class="hl">hello@deskhavenmail.com</li></ul>
    </div>
  </footer>
</div>
</body>
</html>
```